Gardener needs an exciting new flyer design.

I'm a passionate gardener that requires a custom flyer design for a owner operator gardening business. Design will be for a DL flyer. I'm based on the Sunshine coast in Queensland Australia. My target audience is the residential market on the Sunshine coast. Business name is Marlowe Grove. My services are, lawn mowing, weeding, Eco Friendly fertilizing, green waste removal, Mulching, tree and shrub pruning, Full garden makeovers, hedging, pressure cleaning, privacy screening, Timber deck rejuvenation, Planting, Turf preparation and installation, and much more. Free no obligation quotes, reliable and friendly service, great rates. 12 years experience. Web www.marlowegrove.com.au - Phone 0481527306 - Email tom@marlowegrove.com.au I would like the design to portray a friendly and professional approach.

Target Market(s)

Residential

Industry/Entity Type

Gardener

Font styles to use
Serif

Colors
9ccb3b
abd037
3176b5

Requirements
Must have
• my services, my logo, my contact details,

```html
<!DOCTYPE html>
<html lang="en">
<head>
<meta charset="utf-8">
<title>Marlowe Grove – DL Flyer</title>
<link rel="stylesheet" href="https://fonts.googleapis.com/css2?family=Roboto+Slab:wght@700;800&family=Open+Sans:wght@400;600&family=Montserrat:wght@400&display=swap">
<style>
  :root {
    --bg: #5e5e5e;
    --paper: #ffffff;
    --paper-top: #f4f4f4;
    --purple: #5c2363;
    --purple-text: #5a1f60;
    --green: #2f8a2f;
    --green-light: #9ccb3b;
    --green-bright: #abd037;
    --lawn: #4f9f2e;
    --lawn-deep: #3f7f2f;
    --sky: #3fa6e2;
    --ink: #222222;
    --white: #ffffff;
  }
  * { box-sizing: border-box; margin: 0; padding: 0; }
  html, body { width: 1200px; height: 1200px; overflow: hidden; background: var(--bg); }
  .stage { position: relative; width: 1200px; height: 1200px; }
  .flyer {
    position: absolute; top: 189px; width: 392px; height: 832px;
    background: var(--paper); overflow: hidden;
    font-family: "Open Sans", sans-serif; color: var(--ink);
  }
  .flyer--front { left: 126px; }
  .flyer--back { left: 620px; }
  .abs { position: absolute; left: 0; width: 100%; }

  /* front */
  .front-top { top: 0; height: 190px; background: var(--paper-top); }
  .brand { top: 52px; text-align: center; }
  .brand__dot { display: block; width: 58px; height: 58px; border-radius: 50%; background: var(--green); margin: 0 auto 16px; }
  .brand__name { font-family: "Roboto Slab", serif; font-weight: 700; font-size: 25px; color: var(--green); }
  .hero-photo { top: 180px; height: 370px;
    background: linear-gradient(180deg, var(--lawn-deep) 0%, var(--lawn) 100%); }
  .hero-title { top: 414px; text-align: center; font-family: "Roboto Slab", serif; font-weight: 700;
    font-size: 22px; line-height: 28px; color: var(--white); text-shadow: 0 1px 3px rgba(0,0,0,.35); }
  .wave { position: absolute; left: 0; width: 392px; }
  .welcome { top: 530px; text-align: center; font-family: "Roboto Slab", serif; font-weight: 800;
    font-size: 23px; line-height: 28px; color: var(--purple-text); }
  .intro { top: 597px; padding: 0 30px; text-align: center; font-size: 10px; line-height: 13.6px; }
  .intro p + p { margin-top: 14px; }
  .footer-url { top: 790px; text-align: center; font-family: "Montserrat", sans-serif; font-size: 14px;
    letter-spacing: 1.2px; color: var(--white); }

  /* back */
  .house-photo { top: 0; height: 380px;
    background: linear-gradient(180deg, var(--sky) 0%, var(--lawn) 100%); }
  .section-title { text-align: center; font-family: "Roboto Slab", serif; font-weight: 800; font-size: 19.5px; color: var(--purple-text); }
  .services { position: absolute; display: grid; grid-template-columns: 174px 184px; left: 34px; }
  .services ul { list-style: none; }
  .services li { position: relative; padding-left: 20px; font-size: 11.5px; line-height: 15px; font-weight: 600; color: #2a2a2a; margin-bottom: 10px; }
  .services li svg { position: absolute; left: 0; top: 1px; width: 12px; height: 12px; }
  .contacts { top: 742px; text-align: center; font-family: "Montserrat", sans-serif; color: var(--white); font-size: 15px; line-height: 23px; }
  .contacts svg { width: 11px; height: 11px; vertical-align: -1px; margin-right: 4px; }
</style>
</head>
<body>
<div class="stage">

  <section class="flyer flyer--front">
    <div class="abs front-top"></div>
    <div class="abs hero-photo" role="img" aria-label="Photo of a landscaped garden with a green lawn, flower beds and tall trees"></div>
    <div class="abs brand">
      <span class="brand__dot"></span>
      <span class="brand__name">Marlowe Grove</span>
    </div>
    <h1 class="abs hero-title">A BEAUTIFUL GARDEN<br>DOESN'T HAPPEN BY ITSELF</h1>
    <svg class="wave" style="top:490px" height="70" viewBox="0 0 392 70" aria-hidden="true">
      <defs><linearGradient id="gf" x1="0" x2="1"><stop offset="0" stop-color="#2f8a2f"/><stop offset="1" stop-color="#abd037"/></linearGradient></defs>
      <path d="M0 34 Q200 -6 392 40 L392 70 L0 70Z" fill="url(#gf)"/>
      <path d="M0 42 Q200 4 392 46 L392 70 L0 70Z" fill="#fff"/>
    </svg>
    <h2 class="abs welcome">WELCOME TO<br>MARLOWE GROVE</h2>
    <div class="abs intro">
      <p>Marlowe Grove is your garden &amp; lawn care specialist, with a passion for gardening and a keen eye for detail you can rest assured you're in the right hands.</p>
      <p>My services are tailored to meet every individual clients needs. From a one time mow too regular lawn mowing, all aspects of garden care and even full garden makeovers.</p>
      <p>I go that extra mile every time to leave you garden and yard looking amazing.</p>
    </div>
    <svg class="wave" style="top:725px" height="107" viewBox="0 0 392 107" aria-hidden="true">
      <defs><linearGradient id="gb" x1="0" x2="1"><stop offset="0" stop-color="#2f8a2f"/><stop offset="1" stop-color="#abd037"/></linearGradient></defs>
      <path d="M0 4 Q190 62 392 18 L392 24 Q190 66 0 14Z" fill="url(#gb)"/>
      <path d="M0 22 Q190 72 392 30 L392 107 L0 107Z" fill="#5c2363"/>
    </svg>
    <p class="abs footer-url">www.marlowegrove.com.au</p>
  </section>

  <section class="flyer flyer--back">
    <div class="abs house-photo" role="img" aria-label="Photo of a Queenslander house with manicured hedges, lawn and a concrete driveway under blue sky"></div>
    <svg class="wave" style="top:320px" height="70" viewBox="0 0 392 70" aria-hidden="true">
      <defs><linearGradient id="gf2" x1="0" x2="1"><stop offset="0" stop-color="#2f8a2f"/><stop offset="1" stop-color="#abd037"/></linearGradient></defs>
      <path d="M0 34 Q200 -6 392 40 L392 70 L0 70Z" fill="url(#gf2)"/>
      <path d="M0 44 Q200 6 392 50 L392 70 L0 70Z" fill="#fff"/>
    </svg>

    <h2 class="abs section-title" style="top:377px">GARDEN SERVICES</h2>
    <div class="services" style="top:421px">
      <ul>
        <li><svg viewBox="0 0 12 12"><path d="M1 6.5l3 3 7-7" fill="none" stroke="#2f8a2f" stroke-width="2"/></svg>Lawn mowing</li>
        <li><svg viewBox="0 0 12 12"><path d="M1 6.5l3 3 7-7" fill="none" stroke="#2f8a2f" stroke-width="2"/></svg>Fertilizing</li>
        <li><svg viewBox="0 0 12 12"><path d="M1 6.5l3 3 7-7" fill="none" stroke="#2f8a2f" stroke-width="2"/></svg>Garden mulching</li>
        <li><svg viewBox="0 0 12 12"><path d="M1 6.5l3 3 7-7" fill="none" stroke="#2f8a2f" stroke-width="2"/></svg>Hedging</li>
        <li><svg viewBox="0 0 12 12"><path d="M1 6.5l3 3 7-7" fill="none" stroke="#2f8a2f" stroke-width="2"/></svg>Weeding</li>
      </ul>
      <ul>
        <li><svg viewBox="0 0 12 12"><path d="M1 6.5l3 3 7-7" fill="none" stroke="#2f8a2f" stroke-width="2"/></svg>Turf preparation and<br>installation</li>
        <li><svg viewBox="0 0 12 12"><path d="M1 6.5l3 3 7-7" fill="none" stroke="#2f8a2f" stroke-width="2"/></svg>Tree and shrub pruning</li>
        <li><svg viewBox="0 0 12 12"><path d="M1 6.5l3 3 7-7" fill="none" stroke="#2f8a2f" stroke-width="2"/></svg>Full garden makeovers</li>
        <li><svg viewBox="0 0 12 12"><path d="M1 6.5l3 3 7-7" fill="none" stroke="#2f8a2f" stroke-width="2"/></svg>Green waste removal</li>
      </ul>
    </div>

    <h2 class="abs section-title" style="top:573px">OTHER SERVICES</h2>
    <div class="services" style="top:616px">
      <ul>
        <li><svg viewBox="0 0 12 12"><path d="M1 6.5l3 3 7-7" fill="none" stroke="#2f8a2f" stroke-width="2"/></svg>Aluminium fencing &amp;<br>gate installation &amp; repairs</li>
        <li><svg viewBox="0 0 12 12"><path d="M1 6.5l3 3 7-7" fill="none" stroke="#2f8a2f" stroke-width="2"/></svg>Pressure cleaning</li>
      </ul>
      <ul>
        <li><svg viewBox="0 0 12 12"><path d="M1 6.5l3 3 7-7" fill="none" stroke="#2f8a2f" stroke-width="2"/></svg>Timber decking<br>rejuvenation and repairs</li>
        <li><svg viewBox="0 0 12 12"><path d="M1 6.5l3 3 7-7" fill="none" stroke="#2f8a2f" stroke-width="2"/></svg>And much more!</li>
      </ul>
    </div>

    <svg class="wave" style="top:685px" height="147" viewBox="0 0 392 147" aria-hidden="true">
      <defs><linearGradient id="gb2" x1="0" x2="1"><stop offset="0" stop-color="#2f8a2f"/><stop offset="1" stop-color="#abd037"/></linearGradient></defs>
      <path d="M0 4 Q190 62 392 18 L392 24 Q190 66 0 14Z" fill="url(#gb2)"/>
      <path d="M0 22 Q190 72 392 30 L392 147 L0 147Z" fill="#5c2363"/>
    </svg>
    <div class="abs contacts">
      <p><svg viewBox="0 0 12 12"><path d="M3 1l2 2.5-1.2 1.4a7 7 0 0 0 3.3 3.3L8.5 7 11 9l-1.3 2C5 11 1 7 1 2.3Z" fill="#9ccb3b"/></svg>0481527306</p>
      <p><svg viewBox="0 0 12 12"><rect x="0.5" y="2.5" width="11" height="7" fill="#9ccb3b"/><path d="M0.5 2.5l5.5 4 5.5-4" fill="none" stroke="#5c2363" stroke-width="1"/></svg>tom@marlowegrove.com.au</p>
      <p><svg viewBox="0 0 12 12"><circle cx="6" cy="6" r="5" fill="none" stroke="#9ccb3b" stroke-width="1.4"/><path d="M1 6h10M6 1c-3 3-3 7 0 10M6 1c3 3 3 7 0 10" fill="none" stroke="#9ccb3b" stroke-width="1"/></svg>www.marlowegrove.com.au</p>
    </div>
  </section>

</div>
</body>
</html>
```